Create a memorable Stationary for Security Software Company

Velbrantix is the worldwide leader in securing the Internet. Making Internet communications and critical data secure, reliable and available everywhere has been and continues to be our ongoing vision. We are committed to staying focused on real customer needs and to developing new and innovative security solutions that redefine the security landscape.

Industry/Entity Type

Internet

Font styles to use
Serif
Sans Serif
Script

Colors
0792cd
33a6d7
85cae6

```html
<!DOCTYPE html>
<html lang="en">
<head>
<meta charset="utf-8">
<title>Velbrantix Business Card</title>
<link href="https://fonts.googleapis.com/css2?family=Open+Sans:wght@400;600&display=swap" rel="stylesheet">
<style>
  :root {
    --page: #2b2a29;
    --card: #141414;
    --blue-deep: #0792cd;
    --blue: #33a6d7;
    --blue-light: #85cae6;
    --text: #f2f2f2;
    --divider: #5a5a5a;
  }
  * { box-sizing: border-box; margin: 0; padding: 0; }
  html, body { width: 1200px; height: 814px; overflow: hidden; }
  body {
    background: var(--page);
    font-family: "Open Sans", Arial, sans-serif;
    position: relative;
  }
  .card {
    position: absolute;
    top: 252px;
    width: 525px;
    height: 310px;
    background: var(--card);
    box-shadow: 0 6px 18px rgba(0,0,0,.45);
  }
  .card--front { left: 50px; }
  .card--back { left: 625px; }

  /* front */
  .brand {
    position: absolute;
    left: 0; top: 0;
    width: 262px; height: 310px;
    display: flex; flex-direction: column;
    align-items: center; justify-content: center;
    gap: 16px;
  }
  .brand__dot {
    width: 74px; height: 74px;
    border-radius: 50%;
    background: var(--blue);
  }
  .brand__name {
    color: var(--blue);
    font-size: 27px;
    font-weight: 600;
  }
  .divider {
    position: absolute;
    left: 262px; top: 40px;
    width: 1px; height: 230px;
    background: linear-gradient(to bottom, transparent, var(--divider) 20%, var(--divider) 80%, transparent);
  }
  .details {
    position: absolute;
    left: 290px; top: 56px;
    color: var(--text);
    font-size: 13.5px;
    line-height: 1.45;
  }
  .details__name {
    color: var(--blue);
    font-size: 19px;
    font-weight: 600;
    line-height: 1.2;
  }
  .details__title { margin-bottom: 10px; }
  .details__address { margin-bottom: 8px; }
  .contact { list-style: none; }
  .contact li { display: flex; align-items: center; gap: 10px; }
  .contact svg { width: 13px; height: 13px; flex: none; fill: var(--blue); }

  /* back */
  .back__mark {
    position: absolute;
    left: 50%; top: 62px;
    transform: translateX(-50%);
    display: flex; flex-direction: column; align-items: center; gap: 14px;
  }
  .back__dot {
    width: 120px; height: 120px;
    border-radius: 50%;
    background: var(--blue);
  }
  .back__name {
    color: var(--blue);
    font-size: 22px;
    font-weight: 600;
  }
  .back__web {
    position: absolute;
    left: 0; right: 0; bottom: 40px;
    text-align: center;
    color: var(--blue-deep);
    font-size: 12px;
    letter-spacing: 5px;
  }
</style>
</head>
<body>
  <section class="card card--front">
    <div class="brand">
      <div class="brand__dot"></div>
      <div class="brand__name">Velbrantix</div>
    </div>
    <div class="divider"></div>
    <div class="details">
      <p class="details__name">Mara Ellison</p>
      <p class="details__title">CEO/Founder</p>
      <p class="details__address">4120 Larkspur Way<br>Juneau, Alaska 34512</p>
      <ul class="contact">
        <li>
          <svg viewBox="0 0 16 16" aria-hidden="true"><path d="M3.5 1l3 3-1.8 1.8c.9 2 2.5 3.6 4.5 4.5L11 8.5l3 3-2 2.5C6.5 13.5 2.5 9.5 1 4z"/></svg>
          512 308 4471
        </li>
        <li>
          <svg viewBox="0 0 16 16" aria-hidden="true"><path d="M4 1h8v4H4zM1 6h14v6h-3v3H4v-3H1zm4 4v4h6v-4z"/></svg>
          517 264 0893
        </li>
        <li>
          <svg viewBox="0 0 16 16" aria-hidden="true"><path d="M1 3h14v10H1zm1.5 1.3V5l5.5 4 5.5-4v-.7z"/></svg>
          hello@velbrantix.com
        </li>
        <li>
          <svg viewBox="0 0 16 16" aria-hidden="true"><circle cx="8" cy="8" r="7"/><path d="M1 8h14M8 1c-3 3-3 11 0 14M8 1c3 3 3 11 0 14" stroke="#141414" stroke-width="1" fill="none"/></svg>
          www.velbrantix.com
        </li>
      </ul>
    </div>
  </section>

  <section class="card card--back">
    <div class="back__mark">
      <div class="back__dot"></div>
      <div class="back__name">Velbrantix</div>
    </div>
    <p class="back__web">www.velbrantix.com</p>
  </section>
</body>
</html>
```